Local fast-growing company in the service sector

We are looking for a modern business card design, which should also appear on our letterheads

Target Market(s)

Private and industrial sectors

Contact Information for Business Card

Vorname Name
Kellberger Str. 18
72845 Lindhausen
Tel.: 07146-839214-0
Name@agentur-kvtl.de

Colors
9d9d9d
919191
aaaaaa

Requirements
Must have
• The logo (file) in silver

```html
<!DOCTYPE html>
<html lang="de">
<head>
<meta charset="utf-8">
<title>KVTL Visitenkarte</title>
<link rel="stylesheet" href="https://fonts.googleapis.com/css2?family=Arimo:wght@400;700&display=swap">
<style>
  :root {
    --bg: #1a1a1a;
    --card: #ffffff;
    --silver: #9d9d9d;
    --silver-mid: #919191;
    --silver-light: #aaaaaa;
    --text: #555555;
    --rule: #d4d4d4;
    --map: #f0f0f0;
    --icon: #999999;
  }
  * { margin: 0; padding: 0; box-sizing: border-box; }
  html, body { width: 1200px; height: 900px; overflow: hidden; }
  body {
    background: var(--bg);
    font-family: "Arimo", Arial, sans-serif;
    color: var(--text);
    position: relative;
  }
  .card {
    position: absolute;
    top: 294px;
    width: 504px;
    height: 288px;
    background: var(--card);
    border-radius: 22px;
    overflow: hidden;
  }
  .card--front { left: 84px; }
  .card--back { left: 606px; }

  .brand {
    position: absolute;
    display: flex;
    align-items: center;
    gap: 18px;
  }
  .brand__mark {
    display: block;
    background: var(--silver-light);
  }
  .brand__name {
    font-weight: 700;
    color: var(--silver);
    letter-spacing: 1px;
    line-height: 1;
  }
  .card--front .brand { left: 28px; top: 58px; }
  .card--front .brand__mark { width: 26px; height: 26px; }
  .card--front .brand__name { font-size: 46px; }

  .holder {
    position: absolute;
    left: 21px;
    right: 20px;
    top: 166px;
    display: flex;
    align-items: flex-end;
    gap: 6px;
  }
  .holder__rule {
    flex: 1;
    border-bottom: 1px solid var(--rule);
  }
  .holder__name {
    font-size: 19px;
    font-weight: 700;
    color: var(--text);
    line-height: 1;
    position: relative;
    top: 3px;
  }

  .address {
    position: absolute;
    left: 26px;
    top: 216px;
    font-size: 13.5px;
    line-height: 17px;
    font-style: normal;
  }
  .address__company { font-weight: 700; }

  .contact {
    position: absolute;
    right: 20px;
    top: 216px;
    font-size: 13.5px;
    line-height: 17px;
    list-style: none;
    text-align: right;
  }
  .contact li {
    display: flex;
    align-items: center;
    justify-content: flex-end;
    gap: 5px;
  }
  .contact svg { width: 12px; height: 12px; flex: none; }

  .world-map {
    position: absolute;
    left: 10px;
    top: 22px;
    width: 484px;
    height: 244px;
    background: radial-gradient(ellipse at center, var(--map) 0%, #f7f7f7 60%, var(--card) 100%);
    border-radius: 8px;
  }
  .card--back .brand { left: 110px; top: 118px; }
  .card--back .brand__mark { width: 32px; height: 32px; }
  .card--back .brand__name { font-size: 56px; }
</style>
</head>
<body>
  <section class="card card--front">
    <div class="brand">
      <span class="brand__mark"></span>
      <span class="brand__name">KVTL</span>
    </div>

    <div class="holder">
      <span class="holder__rule"></span>
      <span class="holder__name">Vorname Name</span>
    </div>

    <address class="address">
      <div class="address__company">KVTL</div>
      <div>Kellberger Str. 18, 72845 Lindhausen</div>
    </address>

    <ul class="contact">
      <li>07146-839214-0
        <svg viewBox="0 0 12 12" aria-hidden="true"><circle cx="6" cy="6" r="6" fill="#999"/><path d="M4 3.2l1 1.2-.6.7c.4.8 1 1.4 1.8 1.8l.7-.6 1.2 1-.6.9c-2 0-3.9-1.9-3.9-3.9z" fill="#fff"/></svg>
      </li>
      <li>Name@agentur-kvtl.de
        <svg viewBox="0 0 12 12" aria-hidden="true"><circle cx="6" cy="6" r="6" fill="#999"/><rect x="3" y="4" width="6" height="4.2" fill="#fff"/><path d="M3 4l3 2.3L9 4" fill="none" stroke="#999" stroke-width=".7"/></svg>
      </li>
    </ul>
  </section>

  <section class="card card--back">
    <div class="world-map" role="img" aria-label="Faint dotted world map in light grey"></div>
    <div class="brand">
      <span class="brand__mark"></span>
      <span class="brand__name">KVTL</span>
    </div>
  </section>
</body>
</html>
```